business card design for a plumbing contractor

i need a double business card for a plumbing business, our initial service is residential Sewer Drain Cleaning.

Target Market(s)

other plumbing Business

Industry/Entity Type

Plumbing

Contact Information for Business Card

www.PipeworksTopMark.example- 5307218394-

Font styles to use
Serif

Colors
ec1f27
0455a3

```html
<!DOCTYPE html>
<html lang="en">
<head>
<meta charset="utf-8">
<title>Pipeworks TopMark – Business Card</title>
<link rel="stylesheet" href="https://fonts.googleapis.com/css2?family=Roboto+Condensed:wght@400;700&display=swap">
<style>
  :root {
    --brand-red: #de3a33;
    --brand-red-strong: #ec1f27;
    --ink-grey: #8a8580;
    --ink-dark: #4a4745;
    --rule-grey: #b9b6b2;
    --card-white: #fbfbfa;
    --stage: #e6e4e0;
    --on-red: #ffffff;
  }
  * { margin: 0; padding: 0; box-sizing: border-box; }
  html, body { width: 1200px; height: 886px; overflow: hidden; }
  body {
    background: var(--stage);
    font-family: "Roboto Condensed", "Arial Narrow", sans-serif;
    position: relative;
  }
  .card {
    position: absolute;
    top: 293px;
    width: 525px;
    height: 300px;
    border-radius: 22px;
    overflow: hidden;
    box-shadow: 0 6px 18px rgba(0,0,0,.18);
  }
  /* Front */
  .card--front { left: 45px; background: var(--card-white); }
  .front__brand {
    position: absolute; top: 40px; right: 40px;
    display: flex; align-items: center; gap: 10px;
  }
  .front__brand-name {
    font-weight: 700; font-size: 30px; line-height: 1;
    color: var(--ink-grey); letter-spacing: .2px;
  }
  .front__brand-mark { width: 18px; height: 18px; background: var(--brand-red-strong); }
  .front__rule {
    position: absolute; left: 30px; right: 40px; top: 188px;
    height: 1px; background: var(--rule-grey);
  }
  .front__rule-accent {
    position: absolute; left: 30px; top: 186px;
    width: 140px; height: 5px; background: var(--brand-red-strong);
  }
  .front__person { position: absolute; left: 30px; top: 130px; }
  .front__name {
    font-size: 24px; font-weight: 400; color: var(--brand-red-strong);
    text-transform: uppercase; line-height: 1.05;
  }
  .front__role {
    font-size: 17px; color: var(--ink-grey); text-transform: uppercase; line-height: 1.2;
  }
  .front__contacts {
    position: absolute; left: 30px; top: 202px;
    list-style: none; font-size: 14px; color: var(--ink-dark);
  }
  .front__contacts li { display: flex; align-items: center; gap: 8px; height: 22px; }
  .front__contacts svg { width: 12px; height: 12px; fill: var(--brand-red-strong); }
  .front__web {
    position: absolute; right: 40px; top: 200px;
    font-size: 14px; color: var(--ink-dark);
  }
  /* Back */
  .card--back { left: 630px; background: var(--brand-red); }
  .back__decor {
    position: absolute; left: 40px; top: -60px;
    width: 260px; height: 260px; border-radius: 50%;
    background: rgba(255,255,255,.08);
  }
  .back__content {
    position: absolute; right: 34px; bottom: 34px;
    text-align: right; color: var(--on-red);
  }
  .back__name { font-weight: 700; font-size: 36px; line-height: 1; margin-bottom: 12px; }
  .back__services { list-style: none; font-size: 16px; line-height: 1.35; }
  .back__services li::after { content: " •"; font-weight: 700; }
</style>
</head>
<body>
  <section class="card card--front" aria-label="Business card front">
    <div class="front__brand">
      <span class="front__brand-name">Pipeworks TopMark</span>
      <span class="front__brand-mark"></span>
    </div>
    <div class="front__person">
      <p class="front__name">Dana Whitfield</p>
      <p class="front__role">CEO/Founder</p>
    </div>
    <div class="front__rule"></div>
    <div class="front__rule-accent"></div>
    <ul class="front__contacts">
      <li>
        <svg viewBox="0 0 24 24" aria-hidden="true"><path d="M6.6 10.8a15.1 15.1 0 0 0 6.6 6.6l2.2-2.2a1 1 0 0 1 1-.25 11.4 11.4 0 0 0 3.6.57 1 1 0 0 1 1 1V20a1 1 0 0 1-1 1A17 17 0 0 1 3 4a1 1 0 0 1 1-1h3.5a1 1 0 0 1 1 1c0 1.25.2 2.45.57 3.57a1 1 0 0 1-.25 1z"/></svg>
        5307218394
      </li>
      <li>
        <svg viewBox="0 0 24 24" aria-hidden="true"><path d="M2 5h20v14H2z M2 5l10 8 10-8" /></svg>
        Dispatcher@PipeworksTopMark.example
      </li>
    </ul>
    <p class="front__web">www.PipeworksTopMark.example</p>
  </section>

  <section class="card card--back" aria-label="Business card back">
    <div class="back__decor"></div>
    <div class="back__content">
      <p class="back__name">Pipeworks TopMark</p>
      <ul class="back__services">
        <li>Sewer Drain Cleaning</li>
        <li>Maintenance</li>
        <li>Trenchless Pipe Installs</li>
      </ul>
    </div>
  </section>
</body>
</html>
```